New business card/stationary for a consulting company

I am looking for a clean and very professional looking business card for my consulting company as well as corresponding stationary. I am uploading our logo. I like simple and powerful for the feel. No graphics but I am open on everything else. Below is my contact information but would like the final to be in a version I can add my employees information into and print. Thank you.

Daniel Whitcombe
dan@ferncliffadvisory.com
2870 North 9th Avenue, Summit Floor, Elm Ridge, Illinois 60531
www.ferncliffadvisory.com

Industry/Entity Type

Consulting

Contact Information for Business Card

Daniel Whitcombe
dan@ferncliffadvisory.com
www.ferncliffadvisory.com

Font styles to use
Serif
Sans Serif

Requirements
Must have
• Our logo and the business card details.
Nice to have
• our website www.ferncliffadvisory.com

```html
<!DOCTYPE html>
<html lang="en">
<head>
<meta charset="utf-8">
<title>Ferncliff Advisory — Business Card</title>
<link href="https://fonts.googleapis.com/css2?family=Cinzel:wght@700&family=Questrial&display=swap" rel="stylesheet">
<style>
  :root {
    --navy: #2c2d78;
    --paper: #f7f7f9;
    --backdrop: #e9eaee;
    --ink-light: #ffffff;
  }
  html, body {
    margin: 0;
    padding: 0;
    width: 1200px;
    height: 802px;
    overflow: hidden;
    background: var(--backdrop);
  }
  .business-card {
    position: absolute;
    left: 180px;
    top: 161px;
    width: 840px;
    height: 480px;
    background: var(--paper);
    box-shadow: 0 6px 24px rgba(0,0,0,0.12);
    overflow: hidden;
  }
  .brand {
    position: absolute;
    left: 0;
    top: 0;
    width: 100%;
    height: 188px;
    text-align: center;
  }
  .brand-mark {
    display: block;
    width: 68px;
    height: 68px;
    margin: 30px auto 0;
    background: var(--navy);
  }
  .brand-name {
    margin: 18px 0 0;
    font-family: "Questrial", sans-serif;
    font-size: 40px;
    font-weight: 400;
    letter-spacing: 1px;
    color: var(--navy);
    line-height: 1;
  }
  .divider {
    position: absolute;
    left: 0;
    top: 190px;
    width: 100%;
    height: 4px;
    background: var(--navy);
  }
  .contact-panel {
    position: absolute;
    left: 0;
    top: 204px;
    width: 100%;
    height: 276px;
    background: var(--navy);
    color: var(--ink-light);
    text-align: right;
    box-sizing: border-box;
    padding: 26px 32px 0 0;
  }
  .person-name {
    margin: 0 0 8px;
    font-family: "Cinzel", serif;
    font-weight: 700;
    font-size: 38px;
    letter-spacing: 3px;
    line-height: 1.1;
  }
  .contact-line {
    margin: 0;
    font-family: "Questrial", sans-serif;
    font-size: 28px;
    line-height: 39px;
  }
</style>
</head>
<body>
  <article class="business-card">
    <header class="brand">
      <span class="brand-mark"></span>
      <h1 class="brand-name">FERNCLIFF ADVISORY</h1>
    </header>
    <div class="divider"></div>
    <section class="contact-panel">
      <h2 class="person-name">Daniel Whitcombe</h2>
      <p class="contact-line">dan@ferncliffadvisory.com</p>
      <p class="contact-line">2870 North 9th Avenue, Summit Floor,</p>
      <p class="contact-line">Elm Ridge, Illinois 60531</p>
      <p class="contact-line">www.ferncliffadvisory.com</p>
    </section>
  </article>
</body>
</html>
```